I need a letterhead for a newsletter that will go out quarterly to the dentists of the 18th district. It is called "The Crestline Digest" We are in Amarillo TX and have this landmark in the photo as our most prominent feature. If it could be used, that would be cool.
This is a professional organization newsletter so the letterhead should be somewhat professional.

Target Market(s)

Dentists

Industry/Entity Type

Dental

Font styles to use
Serif

Colors

Designer to choose only greyscale colors for use in the design.

Requirements
Must have
• I want the title of "The Crestline Digest" to be the on top with the phrase "Cobalt Ridge Dental Society" written underneath.
Nice to have
• the photo incorporated could be incorporated in black and white or color along the bottom of the letterhead or with the title inside the photo.
Should not have
• I don't want it to be cartoony. I want it to be stylish and elegant and professional.

```html
<!DOCTYPE html>
<html lang="en">
<head>
<meta charset="utf-8">
<title>The Crestline Digest – Letterhead</title>
<link rel="stylesheet" href="https://fonts.googleapis.com/css2?family=Cinzel:wght@400;600&family=Didact+Gothic&display=swap">
<style>
  :root {
    --backdrop: #e2e2e4;
    --paper: #f7f7f7;
    --accent: #3a3a3d;
    --ink: #2a2a2c;
    --ink-soft: #55555a;
    --white: #ffffff;
    --photo-dark: #2b2b2e;
    --photo-mid: #8a8a8e;
    --photo-light: #c9c9cc;
    --photo-rock: #6e6e72;
    --photo-ground: #4a4a4d;
  }
  * { box-sizing: border-box; margin: 0; padding: 0; }
  html, body {
    width: 1200px; height: 898px; overflow: hidden;
    background: var(--backdrop);
  }
  .letterhead {
    position: absolute; left: 300px; top: 25px;
    width: 600px; height: 848px;
    background: var(--paper);
    overflow: hidden;
    box-shadow: 0 4px 18px rgba(0, 0, 0, 0.16);
  }
  .top-band {
    position: absolute; left: 0; top: 0; right: 0; height: 20px;
    background: var(--accent);
  }
  .side-band {
    position: absolute; top: 0; right: 0; width: 40px; height: 800px;
    background: var(--accent);
  }
  .hero-frame {
    position: absolute; left: 0; top: 20px; right: 40px; height: 322px;
    background: var(--white);
    border-top-right-radius: 28px;
  }
  .hero {
    position: absolute; left: 0; top: 26px; right: 46px; height: 310px;
    border-top-right-radius: 24px;
    background:
      linear-gradient(180deg, transparent 60%, var(--photo-ground) 100%),
      linear-gradient(90deg, transparent 28%, var(--photo-rock) 36%, var(--photo-mid) 46%, transparent 56%, transparent 82%, var(--photo-rock) 90%, var(--photo-mid) 100%),
      linear-gradient(180deg, var(--photo-dark) 0%, var(--photo-mid) 55%, var(--photo-light) 70%);
  }
  .masthead {
    position: absolute; left: 90px; right: 46px; top: 112px;
    text-align: center; color: var(--white);
    font-family: "Cinzel", Georgia, serif;
    text-shadow: 0 1px 3px rgba(0,0,0,0.45);
  }
  .masthead-title { font-size: 30px; font-weight: 600; letter-spacing: 1px; }
  .masthead-society { font-size: 19px; font-weight: 400; margin-top: 6px; letter-spacing: 0.5px; }
  .letter {
    position: absolute; left: 48px; top: 366px; right: 84px;
    font-family: "Didact Gothic", "Century Gothic", sans-serif;
    color: var(--ink); font-size: 12px; line-height: 1.75;
  }
  .greeting { font-size: 14px; margin-bottom: 6px; }
  .letter p + p { margin-top: 18px; }
  .signature { margin-top: 24px; }
  .signature-name { font-size: 18px; line-height: 1.4; color: var(--ink); }
  .signature-role { font-size: 12px; color: var(--ink-soft); }
  .contact-bar {
    position: absolute; right: 0; bottom: 0; width: 392px; height: 48px;
    background: var(--accent);
    clip-path: polygon(16px 0, 100% 0, 100% 100%, 0 100%);
    display: flex; align-items: center;
    padding-left: 18px;
    font-family: "Didact Gothic", "Century Gothic", sans-serif;
    color: var(--white); font-size: 11px; letter-spacing: 0.4px;
  }
  .contact-item {
    white-space: nowrap; text-align: center; padding: 0 9px;
    border-left: 2px solid var(--white); line-height: 48px;
  }
  .contact-item:first-child { border-left: none; }
</style>
</head>
<body>
  <main class="letterhead">
    <div class="top-band"></div>
    <div class="side-band"></div>
    <div class="hero-frame"></div>
    <div class="hero" role="img" aria-label="Black and white photograph of a sandstone canyon pillar against the sky with canyon land below"></div>
    <header class="masthead">
      <h1 class="masthead-title">The Crestline Digest</h1>
      <h2 class="masthead-society">Cobalt Ridge Dental Society</h2>
    </header>

    <section class="letter">
      <p class="greeting">Hello Sir/Mam</p>
      <p>Lorem ipsum dolor sit amet, consectetur adipiscing elit. Donec orci purus, luctus vitae dignissim eu, iaculis sed purus. Vivamus faucibus, ipsum nec aliquet viverra, leo mauris condimentum ligula, sit amet sagittis enim ligula quis arcu. Nam egestas tortor id nisi porttitor mattis. In tortor ante, ultricies in suscipit a, tempus non massa. Vivamus et auctor mi. Fusce vel massa nulla. Phasellus nec eros mauris, et scelerisque orci. Donec malesuada orci vitae nulla accumsan porta a id massa.</p>
      <p>Quisque accumsan iaculis magna sit amet fringilla. Maecenas consequat, magna eget tincidunt semper, odio nibh rutrum mi, id feugiat ante nisi eu risus. Vestibulum nunc orci, rhoncus a placerat in, ultricies in mi. Cras mattis varius eros, vel fringilla nisi suscipit eget. Quisque scelerisque sagittis nulla at porttitor. Mauris a justo et tellus interdum tristique. Sed id augue vitae urna euismod commodo aliquet a quam. Pellentesque arcu velit, cursus et malesuada ut, consequat et diam. Nullam erat sem, rhoncus id ullamcorper vitae, rhoncus et arcu. In ultricies nulla.</p>
      <div class="signature">
        <div class="signature-name">Owen Hartley</div>
        <div class="signature-role">Co-Founder &amp; CEO</div>
      </div>
    </section>

    <footer class="contact-bar">
      <span class="contact-item">(806) 555-0142</span>
      <span class="contact-item">info@ridgelinemail.com</span>
      <span class="contact-item">www.ridgelinemail.com</span>
    </footer>
  </main>
</body>
</html>
```